Academic and Business book cover

I need a book cover for my academic and business book.
The focus is in international / global negotiation and influence (how to negotiate across cultures).
The book will be published on Zelvorn, both in Vaspet and printed edition. therefore I need something that works under Zelvorn guidelines.The final design should be elegant and still be able to stand out against the competition.
I would like to have orange+grey for the text colors on the cover, even if different options are welcome.
Title and my name are in the attached word doc.

Target Market(s)

graduates, Phds, from international business schools. Managers

Industry/Entity Type

Business

Font styles to use
Serif
Sans Serif

Colors

Designer to choose colors to be used in the design.

Requirements
Must have
• The title and my name should have elegant fonts.
Nice to have
• pictures of the world that don't have the "usual" Europe in the centre.

```html
<!DOCTYPE html>
<html lang="en">
<head>
<meta charset="utf-8">
<title>The 3Cs Compass – Book Cover Wrap</title>
<link rel="stylesheet" href="https://fonts.googleapis.com/css2?family=Alegreya:wght@400;500&display=swap">
<style>
  :root {
    --page-bg: #ffffff;
    --cover-black: #050607;
    --cover-blue-deep: #0d3a52;
    --cover-blue-mid: #145a7c;
    --glow-blue: #1f8fd6;
    --land-grey: #3a3c40;
    --title-orange: #f2a01a;
    --subtitle-grey: #b9bcc0;
    --text-white: #eef0f2;
    --isbn-grey: #c9c9c9;
    --isbn-text: #333333;
  }

  html, body {
    margin: 0;
    padding: 0;
    width: 1200px;
    height: 857px;
    overflow: hidden;
    background: var(--page-bg);
  }

  .canvas {
    position: relative;
    width: 1200px;
    height: 857px;
    overflow: hidden;
    font-family: "Alegreya", Georgia, serif;
  }

  .cover-wrap {
    position: absolute;
    left: 20px;
    top: 2px;
    width: 1160px;
    height: 852px;
    background: var(--cover-black);
    overflow: hidden;
  }

  /* Back cover */
  .back-cover {
    position: absolute;
    left: 0;
    top: 0;
    width: 563px;
    height: 852px;
    background:
      linear-gradient(to bottom, rgba(20,90,124,0.55) 0%, rgba(5,6,7,0) 14%),
      linear-gradient(to top, rgba(20,90,124,0.85) 0%, rgba(13,58,82,0.35) 22%, rgba(5,6,7,0) 42%),
      radial-gradient(ellipse at 30% 30%, #16191c 0%, var(--cover-black) 70%);
    color: var(--text-white);
  }

  .back-publisher {
    position: absolute;
    left: 21px;
    top: 45px;
    margin: 0;
    font-size: 17.5px;
    font-weight: 400;
  }

  .back-title {
    position: absolute;
    left: 21px;
    top: 92px;
    width: 505px;
    margin: 0;
    font-size: 17px;
    line-height: 23px;
    font-weight: 400;
  }

  .imprint {
    position: absolute;
    right: 7px;
    top: 594px;
    margin: 0;
    text-align: right;
    font-size: 14.5px;
    line-height: 20px;
  }

  .imprint-published {
    position: absolute;
    right: 7px;
    top: 657px;
    margin: 0;
    font-size: 14.5px;
  }

  .isbn-box {
    position: absolute;
    left: 330px;
    top: 691px;
    width: 228px;
    height: 73px;
    background: var(--isbn-grey);
    color: var(--isbn-text);
    font-size: 14px;
    text-align: center;
    padding-top: 8px;
    box-sizing: border-box;
  }

  .catalog-line {
    position: absolute;
    right: 7px;
    top: 790px;
    margin: 0;
    font-size: 14.5px;
  }

  /* Spine */
  .spine {
    position: absolute;
    left: 563px;
    top: 0;
    width: 28px;
    height: 852px;
    background: linear-gradient(to bottom, rgba(20,90,124,0.4) 0%, var(--cover-black) 14%, var(--cover-black) 60%, rgba(20,90,124,0.8) 100%);
  }

  .spine-title,
  .spine-author {
    position: absolute;
    left: 50%;
    margin: 0;
    white-space: nowrap;
    writing-mode: vertical-rl;
    transform: translateX(-50%);
    font-weight: 400;
  }

  .spine-title {
    top: 51px;
    color: var(--title-orange);
    font-size: 17px;
    letter-spacing: 0.5px;
  }

  .spine-author {
    top: 650px;
    color: var(--text-white);
    font-size: 16px;
  }

  /* Front cover */
  .front-cover {
    position: absolute;
    left: 591px;
    top: 0;
    width: 569px;
    height: 852px;
    background:
      linear-gradient(to bottom, rgba(20,90,124,0.6) 0%, rgba(5,6,7,0) 15%),
      linear-gradient(to top, rgba(20,90,124,0.9) 0%, rgba(13,58,82,0.35) 18%, rgba(5,6,7,0) 35%),
      var(--cover-black);
    text-align: center;
  }

  .front-title {
    position: absolute;
    left: 0;
    right: 0;
    top: 30px;
    margin: 0;
    color: var(--title-orange);
    font-size: 52px;
    line-height: 60px;
    font-weight: 400;
    letter-spacing: 0.5px;
    white-space: nowrap;
  }

  .front-subtitle {
    position: absolute;
    left: 0;
    right: 0;
    top: 109px;
    margin: 0;
    color: var(--subtitle-grey);
    font-size: 20.5px;
    line-height: 25px;
    font-weight: 400;
    letter-spacing: 0.3px;
    text-transform: uppercase;
    white-space: nowrap;
  }

  .world-map {
    position: absolute;
    left: 0;
    top: 225px;
    width: 569px;
    height: 370px;
    background:
      radial-gradient(ellipse 48% 44% at 50% 52%, var(--land-grey) 0%, #2b3036 45%, rgba(31,143,214,0.55) 70%, rgba(13,58,82,0.2) 86%, rgba(5,6,7,0) 100%);
  }

  .front-author {
    position: absolute;
    left: 0;
    right: 0;
    top: 786px;
    margin: 0;
    color: var(--title-orange);
    font-size: 20px;
    font-weight: 400;
  }
</style>
</head>
<body>
  <div class="canvas">
    <div class="cover-wrap">

      <section class="back-cover">
        <p class="back-publisher">Ostrel Press – Self Published Book</p>
        <p class="back-title">The 3Cs Compass: Practical Bargaining and Persuasion Methods<br>for Worldwide Leadership</p>

        <p class="imprint">Copyright © 2013 by Darren K. Vallance<br>All Rights Reserved</p>
        <p class="imprint-published">Published in the United States by Ostrel Press</p>
        <div class="isbn-box">ISBN</div>
        <p class="catalog-line">Library of Congress Cataloging in Publication Data</p>
      </section>

      <section class="spine">
        <p class="spine-title">THE 3CS COMPASS</p>
        <p class="spine-author">Darren K. Vallance</p>
      </section>

      <section class="front-cover">
        <h1 class="front-title">THE 3CS COMPASS</h1>
        <h2 class="front-subtitle">Practical Bargaining and Persuasion Methods<br>for Worldwide Leadership</h2>
        <div class="world-map" role="img" aria-label="Dark grey world map with a glowing blue outline radiating light rays"></div>
        <p class="front-author">Darren K. Vallance</p>
      </section>

    </div>
  </div>
</body>
</html>
```